PeakRoamJourneys

1. Can you describe what your company does?

Please find enclosed documents for your reference about our business doing.

2. Who are your target customers for the website?

Company Positioning: A comprehensive supplier of premier international sports travel and high-end event services.
Core Advantage: Exclusive international partnership resources and an Official Ticketing Assurance System.
Service Standard: One-Stop, High-Quality Service Solutions based on the "An once-in-a-lifetime experience" philosophy.

Our target customers for the website:
Mid-to-High-end Sports Enthusiasts
Corporate Clients
Sports Associations
Please kindly find enclosed for more details about our target customers, I think it's very important to make it clear to you.

3. Do you have an existing domain name / website address?

Yes, I have. I just applied for this new domain and it's totally a new website. www.peakroamjourneys.example

4. In addition to a Home Page, which other pages / sections would you like your website to have:
About Us
Contact Us , Office / Mailing Address
Sports Travel Products( Bucket Lists) : Globe Shield, Royal Quartet, Vantara Games, Football, Crestline, Golf, Skiing, Hiking,Galas
Reviews/ Unforgettable Moments
FAQs
Any other page / section you would like: Here is the website for your reference, www.lanewander.example
For each of the pages / sections you’d like to have, please provide the text (and images, if available) you would like to include.
Please recommend 2-3 templates to me, and let me know what kind of text I will provide to every web pages.

5. Which of the below are features and functionalities your website will need:
Image Gallery
Videos
Contact Form
Maps
FAQs
6. Please provide the URLs for the social media profiles you'd like to link to the website.

Do you know Bright Lantern App?

Please let me know anything you need, thank you very much!

Have a good day!

Target Market(s)

Travel for the world-wide sports games and make an once-in-a-lifetime experience

Industry/Entity Type

sports and travel industry

Coding

Number of Pages Required

5+ page

Requirements
Must have
• our logo
Nice to have
• On the homepage, I’d like a banner-style section to prominently showcase the latest products.

```html
<!DOCTYPE html>
<html lang="en">
<head>
<meta charset="utf-8">
<title>About Us — PeakRoamJourneys</title>
<link href="https://fonts.googleapis.com/css2?family=Montserrat:wght@600;700;800;900&family=Open+Sans:wght@400;600;700&display=swap" rel="stylesheet">
<style>
:root{
  --red:#e8414f;
  --red-dark:#c9303d;
  --navy:#1f2a44;
  --navy-deep:#172036;
  --ink:#1c1f2a;
  --text:#6b7280;
  --muted:#8a8f9c;
  --gold:#f0a500;
  --light:#f4f5f8;
  --grey:#e9ecf1;
  --white:#ffffff;
  --footer:#111215;
}
*{box-sizing:border-box;margin:0;padding:0}
html,body{width:1200px;height:4999px;overflow:hidden}
body{font-family:"Open Sans",Arial,sans-serif;color:var(--text);background:var(--light);position:relative}
h1,h2,h3,h4,.display{font-family:"Montserrat",Arial,sans-serif;color:var(--ink)}

/* header */
.site-header{position:absolute;top:0;left:0;width:1200px;height:54px;z-index:5;display:flex;align-items:center;padding:0 76px 0 92px}
.brand{display:flex;align-items:center;gap:7px;font-family:"Montserrat",sans-serif;font-weight:800;font-size:15px;color:var(--red)}
.brand-mark{width:12px;height:12px;background:var(--red)}
.nav{display:flex;align-items:center;gap:28px;margin-left:auto;font-size:12px;font-weight:600;color:#fff}
.nav .active{background:var(--red);padding:8px 12px;border-radius:16px}
.lang{display:flex;align-items:center;gap:6px}
.lang i{width:10px;height:10px;border-radius:50%;background:#fff;display:block}
.btn-book{background:var(--red);color:#fff;font-family:"Montserrat",sans-serif;font-weight:700;font-size:11px;letter-spacing:1px;padding:10px 20px;border-radius:18px}

/* hero */
.hero{position:absolute;top:0;left:0;width:1200px;height:462px;background:linear-gradient(180deg,#3a4358 0%,#2c3550 50%,#232c44 100%);text-align:center;color:#fff}
.hero h1{color:#fff;font-size:56px;font-weight:900;padding-top:168px;letter-spacing:1px}
.hero p{font-size:18px;line-height:31px;width:600px;margin:18px auto 0;color:#e9ebf2}

.sec-title{font-size:38px;font-weight:900;text-align:center;letter-spacing:.5px}
.bar{width:78px;height:4px;background:var(--red);margin:16px auto 0;border-radius:2px}
.sec-sub{text-align:center;font-size:17px;line-height:28px;width:600px;margin:0 auto;color:var(--muted)}

/* about intro */
.about-intro{position:absolute;top:462px;left:0;width:1200px;height:272px;background:var(--light);border-bottom:1px solid #e3e6ec}
.about-intro h2{margin-top:97px}
.about-intro .sec-sub{margin-top:34px;width:600px}

/* story */
.story{position:absolute;top:734px;left:0;width:1200px;height:658px;background:var(--light)}
.story-photo{position:absolute;left:83px;top:159px;width:492px;height:290px;border-radius:12px;background:linear-gradient(180deg,#1c2c56 0%,#26386a 40%,#3e7a33 70%,#2e5e25 100%);box-shadow:0 14px 30px rgba(20,30,60,.25);transform:rotate(-1deg)}
.story-text{position:absolute;left:631px;top:22px;width:490px}
.story-text h3{font-size:28px;font-weight:800}
.story-text p{font-size:13.5px;line-height:24px;margin-top:18px;color:var(--muted)}
.story-text p:first-of-type{margin-top:26px}
.btn-pill{display:inline-flex;align-items:center;gap:8px;background:var(--red);color:#fff;font-family:"Montserrat",sans-serif;font-weight:700;font-size:11px;letter-spacing:1.2px;padding:15px 32px;border-radius:24px;margin-top:28px;box-shadow:0 8px 18px rgba(232,65,79,.35)}

/* moments */
.moments{position:absolute;top:1392px;left:0;width:1200px;height:923px;background:linear-gradient(180deg,#1f2a44 0%,#1c2640 100%);text-align:center}
.moments h2{color:#fff;margin-top:95px}
.moments .bar{background:var(--gold)}
.moments .sec-sub{color:#e2e5ee;margin-top:36px;width:540px}
.video{position:absolute;left:76px;top:354px;width:1060px;height:472px;border-radius:14px;background:radial-gradient(ellipse at 50% 40%,#5b6474 0%,#3a4253 45%,#1f2535 100%);color:#fff}
.video h3{color:#fff;font-size:34px;font-weight:800;margin-top:118px}
.video p{font-size:15.5px;line-height:27px;width:540px;margin:14px auto 0}
.play{width:62px;height:62px;border-radius:50%;background:var(--red);margin:28px auto 0;display:flex;align-items:center;justify-content:center}

/* advantages */
.advantages{position:absolute;top:2315px;left:0;width:1200px;height:753px;background:var(--grey)}
.advantages h2{margin-top:96px}
.advantages .sec-sub{margin-top:34px;width:560px}
.adv-card{position:absolute;top:316px;width:237px;height:340px;background:#fff;border-radius:8px;border-top:4px solid var(--red);text-align:center;padding:28px 30px 0;box-shadow:0 6px 18px rgba(30,40,70,.07)}
.adv-card h4{font-size:17px;font-weight:800;line-height:21px;margin-top:12px}
.adv-card p{font-size:12px;line-height:20px;margin-top:14px;color:var(--muted)}

/* clients */
.clients{position:absolute;top:3068px;left:0;width:1200px;height:610px;background:var(--light)}
.client-card{position:absolute;top:92px;width:326px;height:423px;background:#fff;border-radius:8px;border-top:4px solid var(--red);padding:34px 32px 0;box-shadow:0 6px 18px rgba(30,40,70,.07)}
.client-card h4{font-size:21px;font-weight:800;text-align:center}
.client-card p{font-size:13.5px;line-height:24px;text-align:center;margin-top:12px;color:var(--muted)}
.client-card ul{list-style:none;margin-top:22px}
.client-card li{position:relative;font-size:12px;line-height:18px;padding-left:20px;margin-bottom:14px;color:#3a3f4c}
.client-card li::before{content:"";position:absolute;left:2px;top:6px;width:7px;height:7px;border-radius:50%;background:var(--red)}

/* contact */
.contact{position:absolute;top:3678px;left:0;width:1200px;height:924px;background:var(--light)}
.contact h2{margin-top:93px}
.contact .sec-sub{margin-top:42px;width:560px}
.card{position:absolute;background:#fff;border-radius:8px;box-shadow:0 6px 20px rgba(30,40,70,.08)}
.hq{left:74px;top:317px;width:499px;height:270px;padding:30px 32px}
.card h3{font-size:24px;font-weight:800;white-space:nowrap}
.hq h3{font-size:22px}
.info-row{display:flex;align-items:center;gap:18px;font-size:13.5px;margin-top:20px;color:var(--muted);white-space:nowrap}
.info-row:first-of-type{margin-top:26px}
.info-row svg{flex:none}
.map{left:74px;top:620px;width:499px;height:237px;background:linear-gradient(135deg,#e7ebe6 0%,#dfe6ee 55%,#d7e3d3 100%)}
.details{left:621px;top:317px;width:500px;height:569px;padding:30px 32px}
.details .info-row{font-size:13px}
.hours h4{font-size:17px;font-weight:700;margin-top:40px}
.hours-row{display:flex;justify-content:space-between;font-size:12px;padding:11px 0 10px;border-bottom:1px solid #eceef2;color:var(--muted)}
.hours-row b{color:var(--ink);font-weight:700}

/* footer */
.site-footer{position:absolute;top:4602px;left:0;width:1200px;height:397px;background:var(--footer);color:#b9bcc4}
.f-col{position:absolute;top:52px;width:250px}
.f-col h5{font-family:"Montserrat",sans-serif;font-weight:800;font-size:17px;color:var(--red);letter-spacing:.3px}
.f-col p{font-size:12.5px;line-height:24px;margin-top:24px;color:#c9ccd3}
.f-list{list-style:none;margin-top:22px}
.f-list li{display:flex;align-items:center;gap:14px;font-size:12.5px;margin-bottom:15px;color:#c9ccd3;white-space:nowrap}
.socials{display:flex;gap:16px;margin-top:20px}
.socials span{width:34px;height:34px;border-radius:50%;background:#25272d;display:block}
.copyright{position:absolute;left:76px;right:76px;top:362px;border-top:1px solid #2a2c32;text-align:center;font-size:11px;color:#8d9099}
.copyright span{display:block;margin-top:10px}
</style>
</head>
<body>

<header class="site-header">
  <div class="brand"><span class="brand-mark"></span>PeakRoamJourneys</div>
  <nav class="nav">
    <span>Home</span><span>Featured Sports</span><span>Packages &amp; Services</span>
    <span class="active">About Us</span><span>Contact Us</span>
    <span class="lang"><i></i>English
      <svg width="10" height="6" viewBox="0 0 10 6"><path d="M1 1l4 4 4-4" stroke="#fff" stroke-width="1.6" fill="none"/></svg></span>
    <span class="btn-book">BOOK NOW</span>
  </nav>
</header>

<section class="hero" role="img" aria-label="Stadium crowd and football players in action, dark blue overlay">
  <h1>ABOUT US</h1>
  <p>A comprehensive supplier of premier international sports travel and high-end event service since 2014</p>
</section>

<section class="about-intro">
  <h2 class="sec-title">ABOUT PEAKROAMJOURNEYS</h2>
  <div class="bar"></div>
  <p class="sec-sub">A comprehensive supplier of premier international sports travel and high-end event service since 2014</p>
</section>

<section class="story">
  <div class="story-photo" role="img" aria-label="Floodlit cricket stadium at dusk"></div>
  <div class="story-text">
    <h3>Our Story</h3>
    <p>PeakRoamJourneys began with a simple passion: to bring sports enthusiasts closer to the events they love. Founded in 2014, we've grown from a small startup to a premier provider of international sports travel experiences.</p>
    <p>Our journey started when our founder, a lifelong sports fan, struggled to get tickets and arrange travel for major international events. Recognizing this gap in the market, we set out to create seamless, unforgettable experiences for fellow sports lovers.</p>
    <p>Today, we partner with top sports organizations worldwide to offer exclusive access, premium seating, and comprehensive travel packages. From Globe Shield finals to Vantara Games, we've helped thousands of clients create memories that last a lifetime.</p>
    <p>What sets us apart is our dedication to personalized service. We don't just sell packages; we craft experiences tailored to each client's preferences, ensuring every journey is as unique as the sports moments they're traveling to witness.</p>
    <span class="btn-pill">OUR ADVANTAGES
      <svg width="10" height="10" viewBox="0 0 10 10"><path d="M1 5h7M5 2l3 3-3 3" stroke="#fff" stroke-width="1.5" fill="none"/></svg></span>
  </div>
</section>

<section class="moments">
  <h2 class="sec-title">SPORTS TRAVEL MOMENTS</h2>
  <div class="bar"></div>
  <p class="sec-sub">Experience the excitement and passion of our premium sports travel adventures</p>
  <div class="video" role="img" aria-label="Cheering fans in a stadium with confetti, video preview">
    <h3>Sports Travel Moments</h3>
    <p>Join us on an exclusive journey to the world's most prestigious sporting events. Experience premium access, luxury accommodations, and unforgettable moments that will last a lifetime.</p>
    <div class="play"><svg width="20" height="22" viewBox="0 0 20 22"><path d="M4 2l14 9-14 9z" fill="#fff"/></svg></div>
  </div>
</section>

<section class="advantages">
  <h2 class="sec-title">OUR PROFESSIONAL ADVANTAGES</h2>
  <div class="bar"></div>
  <p class="sec-sub">Discover what sets PeakRoamJourneys apart in the world of premium sports travel</p>

  <div class="adv-card" style="left:80px">
    <svg width="40" height="46" viewBox="0 0 40 46"><circle cx="20" cy="16" r="13" fill="none" stroke="#e8414f" stroke-width="5"/><circle cx="20" cy="16" r="5" fill="#e8414f"/><path d="M10 27l-4 14 7-3 4 6 3-12M30 27l4 14-7-3-4 6-3-12" fill="#e8414f"/></svg>
    <h4>Professional Qualification</h4>
    <p>Our team consists of certified travel professionals with extensive experience in sports tourism. We hold industry certifications and maintain the highest standards of service excellence.</p>
  </div>
  <div class="adv-card" style="left:350px">
    <svg width="54" height="40" viewBox="0 0 54 40"><path d="M2 8h12l14 4 10-4h14v20H42L30 36l-8-4-10-4H2z" fill="#e8414f"/><path d="M20 14l8 6 6-4" stroke="#fff" stroke-width="2.5" fill="none"/></svg>
    <h4>Resource Advantage</h4>
    <p>We have exclusive partnerships with major sports organizations, venues, and hospitality providers worldwide. This gives our clients access to premium tickets and experiences unavailable to the general public.</p>
  </div>
  <div class="adv-card" style="left:618px">
    <svg width="44" height="44" viewBox="0 0 44 44"><circle cx="22" cy="22" r="19" fill="none" stroke="#e8414f" stroke-width="4"/><ellipse cx="22" cy="22" rx="8" ry="19" fill="none" stroke="#e8414f" stroke-width="3.5"/><path d="M3 22h38M6 12h32M6 32h32" stroke="#e8414f" stroke-width="3"/></svg>
    <h4>All-Encompassing Service</h4>
    <p>From flights and accommodations to event tickets and exclusive experiences, we provide comprehensive travel solutions. Our one-stop service ensures every detail is handled with precision and care.</p>
  </div>
  <div class="adv-card" style="left:888px">
    <svg width="46" height="44" viewBox="0 0 46 44"><path d="M23 2l6.5 13.5 14.5 2-10.5 10 2.5 14.5L23 35l-13 7 2.5-14.5L2 17.5l14.5-2z" fill="#e8414f"/></svg>
    <h4>Client Experience</h4>
    <p>We prioritize creating unforgettable moments for our clients. Our personalized approach, attention to detail, and commitment to excellence ensure every journey exceeds expectations.</p>
  </div>
</section>

<section class="clients">
  <div class="client-card" style="left:80px">
    <h4>Sports Enthusiasts</h4>
    <p>Individual fans and groups who want to experience the thrill of live sports events around the world with premium access and exclusive experiences.</p>
    <ul><li>Premium event tickets and seating</li><li>Exclusive behind-the-scenes access</li><li>Meet-and-greet opportunities with athletes</li><li>Customized travel itineraries</li><li>VIP hospitality packages</li></ul>
  </div>
  <div class="client-card" style="left:439px">
    <h4>Corporate Clients</h4>
    <p>Businesses looking to enhance client relationships, reward employees, or host corporate events at world-class sporting venues.</p>
    <ul><li>Corporate hospitality and entertainment</li><li>Client relationship building events</li><li>Employee incentive programs</li><li>Brand activation opportunities</li><li>Executive networking experiences</li></ul>
  </div>
  <div class="client-card" style="left:798px">
    <h4>Sports Associations</h4>
    <p>Sports organizations, teams, and federations requiring travel coordination, event management, and VIP experiences for their members and stakeholders.</p>
    <ul><li>Team travel and accommodation</li><li>Official delegation services</li><li>Sponsor and partner hospitality</li><li>Event management support</li><li>International competition logistics</li></ul>
  </div>
</section>

<section class="contact">
  <h2 class="sec-title">OUR OFFICE LOCATION &amp; CONTACT DETAILS</h2>
  <p class="sec-sub">Visit us or get in touch to start planning your premium sports travel experience</p>

  <div class="card hq">
    <h3>PeakRoamJourneys Headquarters</h3>
    <div class="info-row"><svg width="12" height="16" viewBox="0 0 12 16"><path d="M6 0a6 6 0 016 6c0 4-6 10-6 10S0 10 0 6a6 6 0 016-6z" fill="#e8414f"/><circle cx="6" cy="6" r="2.2" fill="#fff"/></svg>48 Summit Lane, Harbor Vale, NY 10099</div>
    <div class="info-row"><svg width="14" height="14" viewBox="0 0 14 14"><path d="M3 0l3 3-2 2c1 2 3 4 5 5l2-2 3 3-2 3C6 14 0 8 0 3z" fill="#e8414f"/></svg>+1 (555) 010-2841</div>
    <div class="info-row"><svg width="14" height="11" viewBox="0 0 14 11"><rect width="14" height="11" rx="1.5" fill="#e8414f"/><path d="M1 1.5l6 4.5 6-4.5" stroke="#fff" stroke-width="1.3" fill="none"/></svg>info@peakroamjourneys.example</div>
    <div class="info-row"><svg width="14" height="14" viewBox="0 0 14 14"><circle cx="7" cy="7" r="6" fill="none" stroke="#e8414f" stroke-width="1.6"/><path d="M1 7h12M7 1c-3 3-3 9 0 12M7 1c3 3 3 9 0 12" stroke="#e8414f" stroke-width="1.3" fill="none"/></svg>www.peakroamjourneys.example</div>
  </div>

  <div class="card map" role="img" aria-label="Street map showing the headquarters location"></div>

  <div class="card details">
    <h3>Contact Details</h3>
    <div class="info-row"><svg width="14" height="14" viewBox="0 0 14 14"><circle cx="7" cy="4" r="3.5" fill="#e8414f"/><path d="M0 14c0-4 3-6 7-6s7 2 7 6z" fill="#e8414f"/></svg>General Inquiries: info@peakroamjourneys.example</div>
    <div class="info-row"><svg width="14" height="11" viewBox="0 0 14 11"><rect width="14" height="11" rx="1.5" fill="#e8414f"/><path d="M0 4h14" stroke="#fff" stroke-width="1.4"/></svg>Bookings: bookings@peakroamjourneys.example</div>
    <div class="info-row"><svg width="14" height="14" viewBox="0 0 14 14"><circle cx="7" cy="7" r="5.5" fill="none" stroke="#e8414f" stroke-width="2.5"/><circle cx="7" cy="7" r="2" fill="#e8414f"/></svg>Customer Support: support@peakroamjourneys.example</div>
    <div class="info-row"><svg width="14" height="13" viewBox="0 0 14 13"><rect y="3" width="14" height="10" rx="1.5" fill="#e8414f"/><rect x="4" y="0" width="6" height="4" rx="1" fill="none" stroke="#e8414f" stroke-width="1.5"/></svg>Corporate Services: corporate@peakroamjourneys.example</div>
    <div class="info-row"><svg width="14" height="14" viewBox="0 0 14 14"><path d="M3 0l3 3-2 2c1 2 3 4 5 5l2-2 3 3-2 3C6 14 0 8 0 3z" fill="#e8414f"/></svg>Emergency Contact: +1 (555) 010-7730</div>
    <div class="hours">
      <h4>Business Hours</h4>
      <div class="hours-row"><b>Monday - Friday</b><span>9:00 AM - 6:00 PM EST</span></div>
      <div class="hours-row"><b>Saturday</b><span>10:00 AM - 4:00 PM EST</span></div>
      <div class="hours-row"><b>Sunday</b><span>Closed</span></div>
      <div class="hours-row"><b>Emergency Support</b><span>24/7</span></div>
    </div>
  </div>
</section>

<footer class="site-footer">
  <div class="f-col" style="left:76px;width:240px">
    <h5>PEAKROAMJOURNEYS</h5>
    <p>Premier international sports travel and high-end event services delivering once-in-a-lifetime experiences since 2014. Your trusted partner for exclusive access to the world's most prestigious sporting events.</p>
    <div class="socials"><span></span><span></span><span></span><span></span><span></span></div>
  </div>
  <div class="f-col" style="left:348px">
    <h5>QUICK LINKS</h5>
    <ul class="f-list">
      <li><svg width="7" height="10" viewBox="0 0 7 10"><path d="M1 1l4 4-4 4" stroke="#c9ccd3" stroke-width="1.5" fill="none"/></svg>Home</li>
      <li><svg width="7" height="10" viewBox="0 0 7 10"><path d="M1 1l4 4-4 4" stroke="#c9ccd3" stroke-width="1.5" fill="none"/></svg>Featured Sports</li>
      <li><svg width="7" height="10" viewBox="0 0 7 10"><path d="M1 1l4 4-4 4" stroke="#c9ccd3" stroke-width="1.5" fill="none"/></svg>Packages &amp; Service</li>
      <li><svg width="7" height="10" viewBox="0 0 7 10"><path d="M1 1l4 4-4 4" stroke="#c9ccd3" stroke-width="1.5" fill="none"/></svg>About</li>
    </ul>
  </div>
  <div class="f-col" style="left:618px">
    <h5>SPORTS EVENTS</h5>
    <ul class="f-list">
      <li><svg width="7" height="10" viewBox="0 0 7 10"><path d="M1 1l4 4-4 4" stroke="#c9ccd3" stroke-width="1.5" fill="none"/></svg>Globe Shield</li>
      <li><svg width="7" height="10" viewBox="0 0 7 10"><path d="M1 1l4 4-4 4" stroke="#c9ccd3" stroke-width="1.5" fill="none"/></svg>Royal Quartet Tennis</li>
      <li><svg width="7" height="10" viewBox="0 0 7 10"><path d="M1 1l4 4-4 4" stroke="#c9ccd3" stroke-width="1.5" fill="none"/></svg>Vantara Games</li>
      <li><svg width="7" height="10" viewBox="0 0 7 10"><path d="M1 1l4 4-4 4" stroke="#c9ccd3" stroke-width="1.5" fill="none"/></svg>Crestline Basketball</li>
      <li><svg width="7" height="10" viewBox="0 0 7 10"><path d="M1 1l4 4-4 4" stroke="#c9ccd3" stroke-width="1.5" fill="none"/></svg>Golf Majors</li>
    </ul>
  </div>
  <div class="f-col" style="left:888px">
    <h5>CONTACT US</h5>
    <ul class="f-list">
      <li><svg width="10" height="13" viewBox="0 0 12 16"><path d="M6 0a6 6 0 016 6c0 4-6 10-6 10S0 10 0 6a6 6 0 016-6z" fill="#c9ccd3"/></svg>48 Summit Lane, Harbor Vale</li>
      <li><svg width="12" height="12" viewBox="0 0 14 14"><path d="M3 0l3 3-2 2c1 2 3 4 5 5l2-2 3 3-2 3C6 14 0 8 0 3z" fill="#c9ccd3"/></svg>+1 (555) 010-2841</li>
      <li><svg width="12" height="10" viewBox="0 0 14 11"><rect width="14" height="11" rx="1.5" fill="#c9ccd3"/></svg>info@peakroamjourneys.example</li>
      <li><svg width="12" height="12" viewBox="0 0 14 14"><circle cx="7" cy="7" r="7" fill="#c9ccd3"/><path d="M7 3v4l3 2" stroke="#111215" stroke-width="1.5" fill="none"/></svg>Mon-Fri: 9am-6pm EST</li>
    </ul>
  </div>
  <div class="copyright"><span>© 2025 PeakRoamJourneys. All rights reserved. | Premier Sports Travel Experiences | Established 2014</span></div>
</footer>

</body>
</html>
```